SkyvornQ Business Cards and Stationary Design

Need a design for our business cards and stationary. I want to carry on the theme of the logo. I want the business cards to have a design on the back. I would like the business cards and the stationary to carry the same theme, design scheme, and branding

Target Market(s)

Airlines and Maintenance Facilities

Industry/Entity Type

Aviation

Contact Information for Business Card

Name
Position Title
Address: 4827 Trellis Hollow Road, Fort Pierce, Florida, 34951
Office Number
Mobile Number
Email
Website

Font styles to use
Serif
Sans Serif

Colors

Designer to choose colors to be used in the design.

```html
<!DOCTYPE html>
<html lang="en">
<head>
<meta charset="utf-8">
<title>SkyvornQ Business Cards</title>
<link href="https://fonts.googleapis.com/css2?family=Open+Sans:wght@400;600;700&display=swap" rel="stylesheet">
<style>
  :root {
    --navy: #0c2f6b;
    --blue: #1673c4;
    --sky: #3a9be0;
    --white: #ffffff;
    --ink: #0c2f6b;
    --page: #eceef1;
  }
  * { margin: 0; padding: 0; box-sizing: border-box; }
  html, body { width: 1200px; height: 872px; overflow: hidden; }
  body {
    background: var(--page);
    font-family: "Open Sans", Arial, sans-serif;
    display: flex;
    align-items: center;
    justify-content: center;
    gap: 40px;
  }
  .card {
    position: relative;
    width: 520px;
    height: 300px;
    background: var(--white);
    box-shadow: 0 10px 30px rgba(12, 47, 107, 0.18);
    overflow: hidden;
  }
  .brand {
    display: flex;
    align-items: center;
    gap: 12px;
    color: var(--ink);
    font-weight: 700;
    letter-spacing: 4px;
    text-transform: uppercase;
  }
  .brand-dot {
    border: 5px solid var(--blue);
    border-radius: 50%;
    flex: none;
  }
  /* Logo face */
  .card-logo {
    display: flex;
    flex-direction: column;
    align-items: center;
    justify-content: center;
    gap: 14px;
  }
  .card-logo .brand { font-size: 38px; }
  .card-logo .brand-dot { width: 46px; height: 46px; }
  .card-logo .web {
    color: var(--ink);
    font-size: 14px;
    letter-spacing: 3px;
  }
  /* Contact face */
  .card-contact .backdrop { position: absolute; inset: 0; }
  .card-contact .brand {
    position: absolute;
    left: 26px;
    top: 120px;
    font-size: 27px;
    letter-spacing: 3px;
  }
  .card-contact .brand-dot { width: 36px; height: 36px; border-width: 4px; }
  .details {
    position: absolute;
    right: 26px;
    top: 38px;
    width: 200px;
    color: var(--white);
    text-align: right;
  }
  .person-name { font-size: 18px; font-weight: 700; letter-spacing: 0.3px; }
  .person-role { font-size: 14px; font-weight: 400; margin-bottom: 20px; }
  .contact-list { list-style: none; font-size: 11.5px; line-height: 1.75; }
  .contact-list li { display: flex; justify-content: flex-end; align-items: flex-start; gap: 6px; }
  .contact-list li.address { margin-top: 8px; line-height: 1.45; }
  .contact-list svg { width: 11px; height: 11px; margin-top: 4px; flex: none; }
</style>
</head>
<body>

  <div class="card card-logo">
    <div class="brand"><span class="brand-dot"></span>SkyvornQ</div>
    <div class="web">www.skyvornq.com</div>
  </div>

  <div class="card card-contact">
    <svg class="backdrop" viewBox="0 0 520 300" width="520" height="300" aria-hidden="true">
      <defs>
        <linearGradient id="accent-arc" x1="0" y1="0" x2="0" y2="1">
          <stop offset="0" stop-color="var(--navy)"/>
          <stop offset="0.5" stop-color="var(--sky)"/>
          <stop offset="1" stop-color="var(--white)"/>
        </linearGradient>
      </defs>
      <path d="M262,0 Q352,140 282,300 L520,300 L520,0 Z" fill="var(--navy)"/>
      <path d="M248,0 Q338,135 272,290" fill="none" stroke="url(#accent-arc)" stroke-width="4"/>
    </svg>

    <div class="brand"><span class="brand-dot"></span>SkyvornQ</div>

    <div class="details">
      <div class="person-name">MARCUS DELANEY</div>
      <div class="person-role">PRESIDENT</div>
      <ul class="contact-list">
        <li>
          <svg viewBox="0 0 12 12" fill="none" stroke="currentColor" stroke-width="1"><circle cx="6" cy="6" r="5.4"/><path d="M4 3.2l1 1.4-.6.7a4 4 0 0 0 2.3 2.3l.7-.6 1.4 1-.6 1C6 9 3 6 3.2 4z" fill="currentColor" stroke="none"/></svg>
          012-345-6789
        </li>
        <li>
          <svg viewBox="0 0 12 12" fill="none" stroke="currentColor" stroke-width="1"><circle cx="6" cy="6" r="5.4"/><rect x="4.2" y="2.8" width="3.6" height="6.4" rx="0.6"/></svg>
          012-345-6789
        </li>
        <li>
          <svg viewBox="0 0 12 12" fill="none" stroke="currentColor" stroke-width="1"><circle cx="6" cy="6" r="5.4"/><rect x="3" y="4" width="6" height="4"/><path d="M3 4l3 2.2L9 4"/></svg>
          info@skyvornq.com
        </li>
        <li>
          <svg viewBox="0 0 12 12" fill="none" stroke="currentColor" stroke-width="1"><circle cx="6" cy="6" r="5.4"/><ellipse cx="6" cy="6" rx="2.3" ry="5.4"/><path d="M0.6 6h10.8M1.5 3.5h9M1.5 8.5h9"/></svg>
          www.skyvornq.com
        </li>
        <li class="address">
          <svg viewBox="0 0 12 12" fill="none" stroke="currentColor" stroke-width="1"><circle cx="6" cy="6" r="5.4"/><path d="M6 9.2S3.8 6.8 3.8 5a2.2 2.2 0 0 1 4.4 0C8.2 6.8 6 9.2 6 9.2z"/><circle cx="6" cy="5" r="0.8"/></svg>
          <span>Street Name, City Name<br>Zipcode-012345</span>
        </li>
      </ul>
    </div>
  </div>

</body>
</html>
```